Estate Agent Board Design

Most eye-catching, elegant estate agent board
Company logo should stand out
Korvimark & TREG should be small but visible.

On the board must be:

"FOR SALE"
logos
website zhbproperties.co.uk
tel number 01632 960418

It Company

```html
<!DOCTYPE html>
<html lang="en">
<head>
<meta charset="utf-8">
<title>zhb Sales &amp; Lettings – For Sale Board</title>
<link rel="stylesheet" href="https://fonts.googleapis.com/css2?family=Montserrat:wght@400;700;800;900&display=swap">
<style>
  :root {
    --page: #eef0ee;
    --board-white: #ffffff;
    --green: #1f7a3c;
    --green-dark: #0f4a24;
    --frame: #8c8f92;
    --badge-navy: #1c2f6b;
    --badge-blue: #2c5fb3;
  }
  html, body {
    margin: 0;
    width: 1200px;
    height: 900px;
    overflow: hidden;
    background: var(--page);
  }
  .canvas {
    position: relative;
    width: 1200px;
    height: 900px;
  }
  .sale-board {
    position: absolute;
    left: 281px;
    top: 25px;
    width: 638px;
    height: 850px;
    font-family: "Montserrat", sans-serif;
  }
  .sale-board svg { display: block; width: 100%; height: 100%; }
  .brand-name { font-weight: 800; fill: var(--green-dark); }
  .brand-tagline { font-weight: 700; fill: var(--green-dark); }
  .headline { font-weight: 900; fill: var(--board-white); letter-spacing: 2px; }
  .phone-number { font-weight: 700; fill: var(--board-white); letter-spacing: 1px; }
  .website { font-weight: 400; fill: var(--board-white); letter-spacing: 1.6px; }
  .website-strong { font-weight: 700; }
</style>
</head>
<body>
<main class="canvas">
  <section class="sale-board" aria-label="zhb Sales and Lettings for sale board">
    <svg viewBox="0 0 440 586" xmlns="http://www.w3.org/2000/svg">
      <!-- board face -->
      <rect class="board-face" x="0" y="0" width="440" height="586" fill="var(--board-white)"/>

      <!-- phone bar -->
      <rect class="phone-bar" x="0" y="422" width="440" height="58" fill="var(--green-dark)"/>
      <!-- website bar -->
      <rect class="web-bar" x="0" y="503" width="440" height="36" fill="var(--green)"/>

      <!-- diagonal band -->
      <polygon class="diagonal-band" points="0,586 0,458 418,0 440,0 440,140 30,586" fill="var(--green)"/>
      <line class="band-rule" x1="0" y1="448" x2="409" y2="0" stroke="var(--board-white)" stroke-width="3"/>
      <polygon class="band-edge" points="0,448 0,440 401,0 409,0" fill="var(--green)"/>

      <!-- brand -->
      <rect class="brand-mark" x="20" y="23" width="104" height="105" fill="var(--green-dark)"/>
      <text class="brand-name" x="128" y="100" font-size="96">zhb</text>
      <text class="brand-tagline" x="132" y="126" font-size="13.5">SALES &amp; LETTINGS</text>

      <!-- headline -->
      <text class="headline" x="0" y="0" font-size="72" text-anchor="middle"
            transform="translate(222 292) rotate(-47)">FOR SALE</text>

      <!-- membership badges -->
      <rect class="badge badge-korvimark" x="374" y="291" width="32" height="36" rx="5" fill="var(--badge-navy)"/>
      <circle class="badge badge-treg" cx="390" cy="382" r="21" fill="var(--badge-blue)"/>

      <!-- phone -->
      <path class="phone-icon" fill="var(--board-white)"
            d="M166 441c-3 2-4 6-3 11 2 7 6 13 12 17 3 2 7 2 9-1l2-3-6-5-3 2c-3-2-5-5-6-8l3-2-3-7z"/>
      <text class="phone-number" x="189" y="461" font-size="26">01632 960418</text>

      <!-- website -->
      <text class="website" x="80" y="527" font-size="17">www.<tspan class="website-strong">zhb</tspan>properties.co.uk</text>

      <!-- frame -->
      <rect class="board-frame" x="1.5" y="1.5" width="437" height="583" fill="none" stroke="var(--frame)" stroke-width="3"/>
    </svg>
  </section>
</main>
</body>
</html>
```